Design 4 pages for an event discovery website

This is a contest for the design of 4 pages for an events discovery website. The feature is part of the new sign-up process.

Please see the attached document for a full scope, mockups and the parent category icons.

Target Market(s)

18-35 Australian event goers

Industry/Entity Type

Events

Number of Pages Required

4 page

```html
<!DOCTYPE html>
<html lang="en">
<head>
<meta charset="utf-8">
<title>Evenlo – Sign Up</title>
<link rel="stylesheet" href="https://fonts.googleapis.com/css2?family=Open+Sans:wght@400;600;700&display=swap">
<style>
  :root {
    --ink-light: #ffffff;
    --ink-dark: #111111;
    --brand-orange: #b83f0e;
    --header-veil: rgba(70, 45, 25, 0.55);
    --search-fill: rgba(225, 190, 150, 0.45);
    --search-btn: #3a2c22;
    --signup-fill: rgba(160, 150, 140, 0.55);
    --outline: rgba(255, 255, 255, 0.55);
    --scene-warm: #c8782e;
    --scene-mid: #5a3a3a;
    --scene-dark: #1e1614;
  }
  * { box-sizing: border-box; margin: 0; padding: 0; }
  html, body { width: 1200px; height: 831px; overflow: hidden; }
  body {
    position: relative;
    font-family: "Open Sans", Arial, sans-serif;
    color: var(--ink-light);
    background: var(--scene-dark);
  }
  .hero-backdrop {
    position: absolute; left: 0; top: 0; width: 1200px; height: 746px;
    background:
      radial-gradient(ellipse 420px 260px at 230px 60px, rgba(240,170,60,0.85), transparent 70%),
      radial-gradient(ellipse 300px 200px at 560px 90px, rgba(200,110,110,0.6), transparent 70%),
      radial-gradient(ellipse 160px 260px at 1020px 460px, rgba(200,190,60,0.35), transparent 70%),
      linear-gradient(180deg, var(--scene-warm) 0%, var(--scene-mid) 40%, var(--scene-dark) 85%);
  }
  .site-header {
    position: absolute; left: 0; top: 0; width: 1200px; height: 90px;
    background: var(--header-veil);
  }
  .brand {
    position: absolute; left: 60px; top: 22px;
    font-size: 36px; font-weight: 700; line-height: 44px;
  }
  .nav-link {
    position: absolute; left: 218px; top: 37px;
    font-size: 15px; font-weight: 600;
  }
  .search {
    position: absolute; left: 557px; top: 30px; width: 288px; height: 32px;
    display: flex;
  }
  .search-field { flex: 1; background: var(--search-fill); }
  .search-button {
    width: 29px; background: var(--search-btn);
    display: flex; align-items: center; justify-content: center;
  }
  .auth-button {
    position: absolute; top: 30px; width: 133px; height: 32px;
    display: flex; align-items: center; justify-content: center;
    font-size: 15px; font-weight: 600; text-transform: uppercase;
  }
  .auth-signup { left: 861px; background: var(--signup-fill); color: var(--ink-dark); }
  .auth-login { left: 1000px; background: var(--brand-orange); }
  .signup-title {
    position: absolute; left: 112px; top: 188px;
    font-size: 34px; font-weight: 400;
  }
  .signup-intro {
    position: absolute; left: 112px; top: 248px; width: 940px;
    font-size: 18.5px; line-height: 25px;
  }
  .link-button {
    position: absolute; top: 358px; width: 179px; height: 39px;
    border: 1px solid var(--outline);
    display: flex; align-items: center;
    font-size: 16px; font-weight: 600;
  }
  .link-mark {
    width: 18px; height: 18px; margin-left: 21px;
    border-radius: 50%; background: var(--ink-light);
  }
  .link-divider { width: 1px; height: 22px; background: var(--ink-light); margin-left: 12px; }
  .link-name { flex: 1; text-align: center; padding-right: 10px; }
  .link-status {
    position: absolute; font-size: 11.5px; font-weight: 700; line-height: 18px;
  }
  .carousel-dots {
    position: absolute; left: 561px; top: 717px; display: flex; gap: 12px;
  }
  .dot { width: 10px; height: 10px; border-radius: 50%; border: 1.5px solid var(--ink-light); }
  .dot.is-active { background: var(--ink-light); }
  .site-footer {
    position: absolute; left: 0; top: 746px; width: 1200px; height: 85px;
    background: var(--brand-orange);
  }
  .footer-legal {
    position: absolute; left: 60px; top: 31px; font-size: 17px;
  }
  .footer-legal a { color: var(--ink-light); }
  .footer-social {
    position: absolute; right: 62px; top: 33px; display: flex; gap: 12px;
    font-size: 12px; font-weight: 600;
  }
</style>
</head>
<body>
  <div class="hero-backdrop" role="img" aria-label="Blurred photo of a concert crowd with raised hands facing a lit stage and a performer in yellow"></div>

  <header class="site-header">
    <div class="brand">Evenlo</div>
    <div class="nav-link">Find Events</div>
    <div class="search">
      <div class="search-field"></div>
      <div class="search-button">
        <svg width="13" height="13" viewBox="0 0 13 13" aria-hidden="true">
          <circle cx="5.5" cy="5.5" r="4" fill="none" stroke="#fff" stroke-width="1.5"/>
          <line x1="8.5" y1="8.5" x2="12" y2="12" stroke="#fff" stroke-width="1.5"/>
        </svg>
      </div>
    </div>
    <div class="auth-button auth-signup">Signup</div>
    <div class="auth-button auth-login">Login</div>
  </header>

  <main>
    <h1 class="signup-title">Sign Up</h1>
    <p class="signup-intro">Link in all your other social media accounts and music players By linking your accounts, we can save you a lot of time by<br>automatically determining your interests</p>

    <div class="link-button" style="left:114px"><span class="link-mark"></span><span class="link-divider"></span><span class="link-name">Chirper</span></div>
    <div class="link-button" style="left:308px"><span class="link-mark"></span><span class="link-divider"></span><span class="link-name">Pictora</span></div>
    <div class="link-button" style="left:502px"><span class="link-mark"></span><span class="link-divider"></span><span class="link-name">Tunestream</span></div>
    <div class="link-button" style="left:696px"><span class="link-mark"></span><span class="link-divider"></span><span class="link-name">Songvault</span></div>

    <div class="link-status" style="left:181px; top:407px">Linked</div>
    <div class="link-status" style="left:502px; top:409px">We don’t have that feature yet<br>but have required your interest</div>

    <div class="carousel-dots">
      <span class="dot"></span><span class="dot"></span><span class="dot is-active"></span><span class="dot"></span>
    </div>
  </main>

  <footer class="site-footer">
    <div class="footer-legal">©2015 yoursite - Terms of Service - Privacy - <a href="#">Contact</a></div>
    <div class="footer-social"><span>Circlely</span><span>Chirper</span><span>Orbita</span></div>
  </footer>
</body>
</html>
```